Report-Design  für Social-Media-Beratungs-Agentur
Report-Design für Social-Media-Beratungs-Agentur
Zielgruppe
Wir sind eine Social-Media-Beratungs-Agentur, die KMU bei der strategischen Ausrichtung und Umsetzung ihrer Social-Media-Präsenzen berät und unterstützt.
Aufgabenstellung
Wir analysieren die Vernetra Profile von Unternehmen in einer Excel-Datei, indem wir in einem Reiter verschiedene Aspekte bewerten. Aus diesen Bewertungen ergibt sich dann in einem zweiten Reiter ein Report (hängt hier an), in den die Ergebnisse aus der 1. Mappe automatisch übernommen werden. Dieser Report wird als PDF gespeichert und an den Kunden geschickt. Wir möchten das Report-Design gerne neu gestalten lassen: Es soll zeitgemäß, professionell und kompetent wirken und nicht mehr 'wie in Excel zusammengebastelt'. Ein Beispiel für ein Design, das uns gefällt, hängt als Inspiration an. Gerne können Grafikelemente aus Canva oder anderen Grafikprogrammen eingefügt werden. Wichtig ist, dass die Struktur mit den Zellen, in die Daten automatisch übernommen werden (im Anhang durch # gekennzeichnet), erhalten bleibt. Unsere Firmenfarben sind: #f69f25, #11323a, #809398, #fcfefd. Wir haben noch weitere Analysen, die wir bei Erfolg dieses Auftrags ebenfalls gerne optimieren lassen möchten.

```html
<!DOCTYPE html>
<html lang="en">
<head>
<meta charset="utf-8">
<title>Social Media Consulting Report</title>
<link rel="stylesheet" href="https://fonts.googleapis.com/css2?family=Inter:wght@400;500&display=swap">
<style>
  :root {
    --page: #ecebe7;
    --ink: #15191d;
    --ink-soft: #4e5862;
    --card-green: #d5e0d9;
    --card-sand: #dcd8d0;
    --card-grey: #d8dadd;
    --bar-sage: #9fb1a4;
    --bar-coral: #c77a69;
    --bar-orange: #dea35c;
    --bar-night: #161e26;
    --bar-stone: #b3b3b1;
    --axis: #6f7478;
  }
  * { box-sizing: border-box; margin: 0; padding: 0; }
  html, body { width: 1200px; height: 900px; overflow: hidden; }
  body {
    background: var(--page);
    font-family: "Inter", sans-serif;
    color: var(--ink);
    position: relative;
  }
  .report-title {
    position: absolute; left: 66px; top: 108px;
    font-size: 42px; font-weight: 400; line-height: 51px; letter-spacing: -0.5px;
  }
  .report-intro {
    position: absolute; left: 66px; top: 292px; width: 330px;
    font-size: 17px; line-height: 27px; color: var(--ink-soft);
  }
  .team-photo {
    position: absolute; left: 773px; top: 105px; width: 357px; height: 332px;
    border-radius: 22px;
    background: linear-gradient(160deg, #c9cfd2 0%, #a89684 45%, #6d5846 70%, #2c3a52 100%);
  }
  .metric-card {
    position: absolute; top: 454px; height: 360px; border-radius: 20px;
  }
  .card-profile { left: 73px; width: 345px; background: var(--card-green); }
  .card-performance { left: 431px; width: 341px; background: var(--card-sand); }
  .card-teamwork { left: 787px; width: 345px; background: var(--card-grey); }
  .card-label { position: absolute; left: 38px; top: 36px; font-size: 24px; }
  .card-value { position: absolute; left: 38px; top: 86px; font-size: 24px; }
  .card-sub { position: absolute; left: 38px; top: 88px; font-size: 23px; }
  .card-code { position: absolute; left: 38px; font-size: 18px; }
  .code-top { top: 157px; }
  .code-bottom { top: 296px; font-size: 21px; }
  .big-figure {
    position: absolute; left: 36px; top: 198px;
    display: flex; align-items: center; gap: 10px;
  }
  .big-number { font-size: 66px; letter-spacing: 1px; }
  .network-name { font-size: 20px; color: var(--ink); }
  .chart { position: absolute; left: 0; top: 0; }
  .chart text { font-family: "Inter", sans-serif; font-size: 14px; fill: var(--ink-soft); }
</style>
</head>
<body>
  <h1 class="report-title">Social Media<br>Consulting<br>Report</h1>
  <p class="report-intro">Brief overview of profile results and growth insights, recommendations for better reach and important next steps.</p>
  <div class="team-photo" role="img" aria-label="Photo of a consulting team gathered around a laptop at a meeting table"></div>

  <section class="metric-card card-profile">
    <h2 class="card-label">Vernetra</h2>
    <p class="card-value">912233</p>
    <svg class="chart" width="345" height="360" viewBox="0 0 345 360" aria-hidden="true">
      <rect x="42" y="197" width="42" height="91" rx="21" fill="var(--bar-sage)"/>
      <rect x="104" y="213" width="42" height="75" rx="21" fill="var(--bar-coral)"/>
      <rect x="166" y="160" width="42" height="128" rx="21" fill="var(--bar-orange)"/>
      <rect x="228" y="197" width="42" height="91" rx="21" fill="var(--bar-night)"/>
      <text x="63" y="316" text-anchor="middle">901</text>
      <text x="125" y="316" text-anchor="middle">102</text>
      <text x="187" y="316" text-anchor="middle">144</text>
      <text x="249" y="316" text-anchor="middle">923</text>
    </svg>
  </section>

  <section class="metric-card card-performance">
    <h2 class="card-label">Performance</h2>
    <p class="card-sub">Performance</p>
    <p class="card-code code-top">#9017 g</p>
    <div class="big-figure">
      <span class="big-number">80998</span>
      <span class="network-name">Vernetra</span>
    </div>
    <p class="card-code code-bottom">#FCFEFD</p>
  </section>

  <section class="metric-card card-teamwork">
    <h2 class="card-label">Teamwork</h2>
    <p class="card-value">18288</p>
    <svg class="chart" width="345" height="360" viewBox="0 0 345 360" aria-hidden="true">
      <rect x="40" y="176" width="47" height="104" fill="var(--bar-sage)"/>
      <rect x="97" y="248" width="44" height="32" fill="var(--bar-stone)"/>
      <rect x="152" y="230" width="47" height="50" fill="var(--bar-coral)"/>
      <line x1="40" y1="280.5" x2="303" y2="280.5" stroke="var(--axis)" stroke-width="1.5"/>
      <text x="60" y="316" text-anchor="middle">102</text>
      <text x="128" y="316" text-anchor="middle">807</text>
      <text x="214" y="316" text-anchor="middle">210</text>
      <text x="285" y="316" text-anchor="middle">100</text>
    </svg>
  </section>
</body>
</html>
```